LEARN Business Skills so you can Earn a good living

size of the poster is 8”x 10.75" plus 0.25" bleed.
Please leave 1 inch on the bottoum for footer
I want a design a poster that will attract people's attention.
I appreciate a creative ad however the ad should not take away from being able to clearly read the text.
-I also appreciate a simple creative ad that is not too busy.
-you can use graphics, vectors, or pictures of real people.
-however, if you use real people it should be a white male that is wearing a white shirt and look like a professional person.

Target Market(s)

Potential young business people

Industry/Entity Type

education

Requirements
Must have
• easy to read the text
Nice to have
• I would like a "creative" simple ad that is easy to be read
Should not have
• pictures of women

```html
<!DOCTYPE html>
<html lang="en">
<head>
<meta charset="utf-8">
<title>Learn to Earn – Business Enrichment Course</title>
<link href="https://fonts.googleapis.com/css2?family=Montserrat:wght@400;700;800&family=Great+Vibes&display=swap" rel="stylesheet">
<style>
  :root {
    --stage: #8e8e8e;
    --photo-dark: #111111;
    --photo-mid: #3a3a3a;
    --slate: #5f5f5f;
    --slate-light: #737373;
    --ink-white: #ffffff;
    --footer: #ffffff;
  }
  * { margin: 0; padding: 0; box-sizing: border-box; }
  html, body {
    width: 1200px; height: 1200px; overflow: hidden;
    background: var(--stage);
  }
  .poster {
    position: absolute; left: 177px; top: 44px;
    width: 846px; height: 1112px;
    overflow: hidden;
    font-family: "Montserrat", sans-serif;
    color: var(--ink-white);
  }
  .photo-band {
    position: absolute; left: 0; top: 0; width: 846px; height: 469px;
    background:
      radial-gradient(ellipse 260px 300px at 420px 300px, #e9e9e9 0%, #bdbdbd 35%, rgba(60,60,60,0) 70%),
      linear-gradient(135deg, var(--photo-mid) 0%, #242424 45%, var(--photo-dark) 100%);
  }
  .slate-band {
    position: absolute; left: 0; top: 469px; width: 846px; height: 552px;
    background:
      radial-gradient(ellipse 500px 300px at 600px 250px, var(--slate-light) 0%, rgba(115,115,115,0) 70%),
      var(--slate);
  }
  .footer-band {
    position: absolute; left: 0; top: 1021px; width: 846px; height: 91px;
    background: var(--footer);
  }
  .headline-word {
    position: absolute; font-weight: 800; font-size: 176px; line-height: 1;
    letter-spacing: -3px;
    text-shadow: 0 8px 18px rgba(0,0,0,0.35);
  }
  .headline-learn { left: 112px; top: 318px; }
  .headline-earn { left: 210px; top: 456px; }
  .headline-to {
    position: absolute; left: 100px; top: 472px;
    font-family: "Great Vibes", cursive; font-size: 178px; line-height: 1;
    text-shadow: 0 6px 14px rgba(0,0,0,0.3);
  }
  .course-title {
    position: absolute; right: 469px; top: 648px;
    text-align: right; font-weight: 700; font-size: 53px; line-height: 52.5px;
    letter-spacing: -0.5px;
  }
  .course-tagline {
    position: absolute; right: 469px; top: 820px;
    text-align: right; font-size: 16.6px; line-height: 21.5px; font-weight: 400;
  }
  .benefits-intro {
    position: absolute; left: 463px; top: 665px;
    font-size: 16.5px; font-weight: 400;
  }
  .benefits-list {
    position: absolute; left: 463px; top: 690px;
    font-weight: 700; font-size: 34px; line-height: 44px;
  }
  .topics {
    position: absolute; left: 75px; top: 908px; width: 740px;
    font-weight: 700; font-size: 10.7px; line-height: 18.5px;
    text-transform: uppercase; white-space: nowrap;
  }
</style>
</head>
<body>
  <main class="poster">
    <div class="photo-band" role="img" aria-label="Photo of a smiling bearded businessman in a white shirt holding an open laptop and a fan of dollar bills against a dark wall"></div>
    <div class="slate-band"></div>
    <div class="footer-band"></div>

    <div class="headline-word headline-learn">LEARN</div>
    <div class="headline-to">to</div>
    <div class="headline-word headline-earn">EARN</div>

    <h1 class="course-title">Business<br>Enrichment<br>Course</h1>
    <p class="course-tagline">A proven success of helping<br>people in their livelihoods</p>

    <p class="benefits-intro">Business skills that will help you:</p>
    <p class="benefits-list">Get a quality job -<br>start / grow your<br>business-Increase<br>your salary</p>

    <p class="topics">
      Business Admiistration - Small Business Management -<br>
      Finance - Investments - Computers- Accounting - Sales&nbsp; Marketing - Project Management Interviewing Skills -<br>
      Business Law -Negotiation - Public Speaking - Import/Export - Information Technoloy -Distribution -<br>
      Marketing &nbsp;- &nbsp; Ledgerly - Real Estate - Health Care-Management - Marketnest
    </p>
  </main>
</body>
</html>
```